New Business Card Design for Manufacturing

We are an engineering/manufacturing company that offers Advanced machining/assembly/engineering services, as well as innovative products for the heavy duty engine cooling markets.

We are looking to get a new business card designed that is clean and modern looking, but still fits the wide range of technical/skilled work we do.

- We hope to use this design as the base for other design work in new Presentations, web, and print work.

Industry/Entity Type

Engineering

Contact Information for Business Card

Our preferred color of blue is (RGB) 22/71/159 but can vary slightly from that color. Our content will be our Logo and full company name (Vantrell Forge Works, Inc.), company address, name, job title, phone number with extension, cell number, fax number, website, and email address on the cards.
We'd like the full company name next to the logo, but we are open to other interpretations of that layout.
Preferably, we would like the back side to be clean with just our logo, and the front to contain all of the contact information.

Colors
2f74b4
0355a3
85abd2

Requirements
Must have
• - Logo, company name, needed content - We are open to interpretation beyond that.
• - Standard size business card.
• - Horizontal orientation.
• - Enough space for lengthy names / job titles (for example, a job title could read "Directory of Human Resources" or "V.P. of Governmental Affairs"). We need this to look clean, whether the title be short (CEO) or long (as described above).

```html
<!DOCTYPE html>
<html lang="en">
<head>
<meta charset="utf-8">
<title>Vantrell Forge Works – Business Card</title>
<link rel="stylesheet" href="https://fonts.googleapis.com/css2?family=Open+Sans:wght@400;600;700;800&display=swap">
<style>
  :root {
    --brand-blue: #16479f;
    --brand-blue-deep: #0f4591;
    --brand-blue-mid: #2f74b4;
    --brand-blue-light: #85abd2;
    --ink-grey: #6d6f73;
    --rule-grey: #9a9ca0;
    --paper: #ffffff;
    --paper-shade: #eef0f2;
    --backdrop: #e9eaec;
  }
  * { box-sizing: border-box; margin: 0; padding: 0; }
  html, body {
    width: 1200px; height: 794px; overflow: hidden;
    background: var(--backdrop);
    font-family: "Open Sans", Arial, sans-serif;
  }
  .stage { position: relative; width: 1200px; height: 794px; }

  .card {
    position: absolute; width: 520px; height: 297px;
    border-radius: 3px; overflow: hidden;
    box-shadow: 0 6px 18px rgba(0,0,0,.18);
  }

  /* Back side */
  .card--back {
    left: 70px; top: 150px;
    background: linear-gradient(160deg, var(--brand-blue-mid) 0%, var(--brand-blue-deep) 70%);
  }
  .card--back .world-map {
    position: absolute; left: 70px; top: 30px; width: 400px; height: 180px;
    border-radius: 40%;
    background: radial-gradient(ellipse at center, rgba(133,171,210,.22), rgba(133,171,210,0) 70%);
  }
  .card--back .brand-mark {
    position: absolute; left: 150px; top: 108px;
    display: flex; align-items: center; gap: 12px;
  }
  .brand-mark__square { width: 22px; height: 22px; background: currentColor; }
  .brand-mark__name {
    font-weight: 800; font-size: 44px; letter-spacing: 1px; line-height: 1;
  }
  .card--back .brand-mark { color: var(--paper); }
  .card--back .website {
    position: absolute; left: 205px; top: 228px;
    font-size: 10px; color: var(--brand-blue-light); letter-spacing: .3px;
  }

  /* Front side */
  .card--front {
    left: 610px; top: 350px;
    background: linear-gradient(180deg, var(--paper) 0%, var(--paper-shade) 100%);
  }
  .card--front .band { position: absolute; inset: 0; }
  .card--front .brand-mark {
    position: absolute; right: 38px; top: 42px; color: var(--brand-blue);
  }
  .card--front .brand-mark__name { font-size: 38px; }
  .card--front .brand-mark__square { width: 18px; height: 18px; }

  .holder { position: absolute; left: 32px; top: 124px; }
  .holder__name {
    font-weight: 700; font-size: 19px; color: var(--brand-blue); letter-spacing: .3px;
  }
  .holder__title { font-size: 10px; color: var(--ink-grey); margin-top: 2px; }

  .contact-list {
    position: absolute; left: 32px; top: 200px; list-style: none;
    font-size: 10px; color: var(--paper); line-height: 16px;
  }
  .contact-list li { display: flex; align-items: center; gap: 9px; }
  .contact-list svg { width: 10px; height: 10px; fill: var(--brand-blue-light); }

  .company-address {
    position: absolute; right: 26px; top: 162px; text-align: right;
    font-size: 10px; line-height: 15px; color: var(--paper);
  }
  .company-address__name { color: var(--brand-blue-light); }
</style>
</head>
<body>
<main class="stage">

  <section class="card card--back" aria-label="Business card, back">
    <div class="world-map" role="img" aria-label="Faint world map in the background"></div>
    <div class="brand-mark">
      <span class="brand-mark__square" aria-hidden="true"></span>
      <span class="brand-mark__name">VANTRELL</span>
    </div>
    <p class="website">www.vantrellforge.com</p>
  </section>

  <section class="card card--front" aria-label="Business card, front">
    <svg class="band" viewBox="0 0 520 297" preserveAspectRatio="none" aria-hidden="true">
      <polygon points="298,98 520,98 520,106 292,106" fill="var(--rule-grey)"/>
      <polygon points="190,180 232,180 294,106 300,106 238,180 240,180" fill="var(--brand-blue-light)"/>
      <polygon points="0,182 236,182 296,108 520,108 520,297 0,297" fill="var(--brand-blue-deep)"/>
      <rect x="14" y="122" width="4" height="36" fill="var(--brand-blue)"/>
    </svg>

    <div class="brand-mark">
      <span class="brand-mark__square" aria-hidden="true"></span>
      <span class="brand-mark__name">VANTRELL</span>
    </div>

    <div class="holder">
      <h1 class="holder__name">DANIEL REYES</h1>
      <p class="holder__title">President</p>
    </div>

    <ul class="contact-list">
      <li><svg viewBox="0 0 10 10" aria-label="Phone"><path d="M2 0h2l1 2.5-1.2 1a6 6 0 0 0 2.7 2.7l1-1.2L10 6v2c0 1-1 2-2 2C3.6 10 0 6.4 0 2 0 1 1 0 2 0z"/></svg>+000.000.00.00</li>
      <li><svg viewBox="0 0 10 10" aria-label="Mobile"><path d="M3 0h4a1 1 0 0 1 1 1v8a1 1 0 0 1-1 1H3a1 1 0 0 1-1-1V1a1 1 0 0 1 1-1zm0 1.5v6h4v-6z"/></svg>+000.000.00.00</li>
      <li><svg viewBox="0 0 10 10" aria-label="Fax"><path d="M2.5 0h5v3h-5zM0 3.5h10v4H8V10H2V7.5H0zm3 3V9h4V6.5z"/></svg>+000.000.00.00</li>
      <li><svg viewBox="0 0 10 10" aria-label="Email"><path d="M0 1.5h10v7H0zm1 1v.3L5 5.5l4-2.7v-.3z"/></svg>www.vantrellforge.com</li>
      <li><svg viewBox="0 0 10 10" aria-label="Website"><path d="M5 0a5 5 0 1 1 0 10A5 5 0 0 1 5 0zm0 1.3a3.7 3.7 0 1 0 0 7.4 3.7 3.7 0 0 0 0-7.4z"/></svg>www.vantrellforge.com</li>
    </ul>

    <address class="company-address" style="font-style:normal">
      <span class="company-address__name">Vantrell Forge Works, Inc.</span><br>
      Street Name Avenue, Suite<br>
      100 State, Zip Code,Country
    </address>
  </section>

</main>
</body>
</html>
```